Corporate Travel Technology Company needs new Business Card design

We need a new business card design to reflect our re-branded company. Our company is called tolvEn (pronounced tolvenn) and we provide Business Intelligence and mobile travel management solutions for the corporate travel industry. Our multinational customers use our solutions to manage large travel budgets and frequent travellers, as well as to save money and reduce risk. We'd like to see designs that use the blue and green palette as well as our corporate logo (attached below). The design should communicate innovation, insight, forward thinking, contemporary, trusted.

Target Market(s)

Large multinational corporates and Travel Agencies.

Industry/Entity Type

Business

Contact Information for Business Card

Rosalind Mercer
Chief Executive
tolvEn
Phone number - +61 (0)2 8134 2907
Email address - rosalind.mercer@tolven-example.com
Mobile number - +61 (0)438 516 702
www.tolven-example.com

Font styles to use
Other font styles liked:
• Please use font as close to corporate logo as possible

Colors
0255a3
0393ce
00a990
33b8a4
33a6d7
3176b5

Requirements
Must have
• Please include the words;
• Mobile Travel Management
• Accelerating Travel Business Insights
• Use corporate logo - although icon can be stylised if needed

```html
<!DOCTYPE html>
<html lang="en">
<head>
<meta charset="utf-8">
<title>tolvEn business card</title>
<link rel="stylesheet" href="https://fonts.googleapis.com/css2?family=Open+Sans:wght@400;600&display=swap">
<style>
  :root {
    --page: #e8e5e0;
    --slate: #455c59;
    --slate-dark: #3a4f4c;
    --sky: #2ea3da;
    --paper: #f7f8f8;
    --white: #ffffff;
  }
  * { box-sizing: border-box; margin: 0; padding: 0; }
  html, body {
    width: 1200px; height: 902px; overflow: hidden;
    background: var(--page);
    font-family: "Open Sans", Arial, sans-serif;
  }
  .card {
    position: absolute; left: 260px;
    width: 680px; height: 388px;
    overflow: hidden;
    box-shadow: 0 6px 18px rgba(0,0,0,.18);
  }
  .card--back { top: 43px; background: var(--slate); }
  .card--front { top: 471px; background: var(--paper); }

  .brand {
    position: absolute; display: flex; align-items: center; gap: 18px;
    font-weight: 400; letter-spacing: -1px; line-height: 1; white-space: nowrap;
  }
  .brand__dot { border-radius: 50%; flex: none; }
  .card--back .brand { left: 50%; top: 44%; transform: translate(-50%, -50%); font-size: 120px; color: var(--white); }
  .card--back .brand__dot { width: 70px; height: 70px; border: 8px solid var(--white); }
  .card--front .brand { left: 50%; top: 48px; transform: translateX(-50%); font-size: 96px; color: var(--slate); }
  .card--front .brand__dot { width: 54px; height: 54px; border: 7px solid var(--sky); }

  .tagline {
    position: absolute; left: 0; right: 0; top: 290px;
    text-align: center; color: var(--white); line-height: 1.45;
  }
  .tagline__primary { font-size: 20px; font-weight: 600; letter-spacing: .5px; }
  .tagline__secondary { font-size: 16px; font-weight: 400; opacity: .85; }

  .band { position: absolute; inset: 0; }

  .holder { position: absolute; left: 40px; top: 292px; color: var(--white); white-space: nowrap; }
  .holder__name { font-size: 31px; font-weight: 600; line-height: 1.15; }
  .holder__title { font-size: 22px; font-weight: 400; opacity: .9; }

  .contact {
    position: absolute; left: 372px; top: 280px;
    padding-left: 14px; border-left: 2px solid var(--slate-dark);
    list-style: none; color: var(--white); font-size: 13.5px; line-height: 23px;
  }
  .contact li { display: flex; align-items: center; gap: 10px; white-space: nowrap; }
  .contact svg { width: 14px; height: 14px; flex: none; }
</style>
</head>
<body>

<section class="card card--back" aria-label="Card back">
  <div class="brand"><span class="brand__dot"></span>tolvEn</div>
  <div class="tagline">
    <p class="tagline__primary">Mobile Travel Management</p>
    <p class="tagline__secondary">Accelerating Travel Business Insights</p>
  </div>
</section>

<section class="card card--front" aria-label="Card front">
  <svg class="band" viewBox="0 0 680 388" aria-hidden="true">
    <polygon points="0,248 48,266 614,266 680,128 680,388 0,388" fill="var(--sky)"/>
    <polyline points="22,252 52,262 612,262 668,150" fill="none" stroke="var(--slate-dark)" stroke-width="5" stroke-linejoin="bevel"/>
  </svg>

  <div class="brand"><span class="brand__dot"></span>tolvEn</div>

  <div class="holder">
    <p class="holder__name">Rosalind Mercer</p>
    <p class="holder__title">Chief Executive</p>
  </div>

  <ul class="contact">
    <li>
      <svg viewBox="0 0 16 16" aria-hidden="true"><path d="M4 1h3l1 4-2 1a9 9 0 0 0 4 4l1-2 4 1v3c0 1-1 2-2 2A13 13 0 0 1 1 3c0-1 1-2 3-2z" fill="var(--white)"/></svg>
      +61 (0)2 8134 2907
    </li>
    <li>
      <svg viewBox="0 0 16 16" aria-hidden="true"><rect x="4" y="1" width="8" height="14" rx="1.5" fill="none" stroke="var(--white)" stroke-width="1.6"/><circle cx="8" cy="12.3" r="1" fill="var(--white)"/></svg>
      +61 (0)438 516 702
    </li>
    <li>
      <svg viewBox="0 0 16 16" aria-hidden="true"><circle cx="8" cy="8" r="6.5" fill="none" stroke="var(--white)" stroke-width="1.4"/><ellipse cx="8" cy="8" rx="3" ry="6.5" fill="none" stroke="var(--white)" stroke-width="1.2"/><line x1="1.5" y1="8" x2="14.5" y2="8" stroke="var(--white)" stroke-width="1.2"/></svg>
      www.tolven-example.com
    </li>
    <li>
      <svg viewBox="0 0 16 16" aria-hidden="true"><rect x="1" y="3" width="14" height="10" rx="1" fill="none" stroke="var(--white)" stroke-width="1.4"/><polyline points="1.5,3.5 8,9 14.5,3.5" fill="none" stroke="var(--white)" stroke-width="1.4"/></svg>
      rosalind.mercer@tolven-example.com
    </li>
  </ul>
</section>

</body>
</html>
```